Fitness Equipment Repair Business Needs a Catchy New Business Card

We have an existing business card, however, it is quite plain and boring. We are expanding primarily in the commercial area (gyms, studios, apartment complexes etc). The business card will serve as eye candy to those managers/owners that can't be met for a face to face.
Originally I was planning for a brochure as well, but all of our information is better summarized on our website. (brightloopservice.ca).
I would like the card to match the colour scheme of the website and utilize the logo. It should have a professional clean feel to it, however, a little colouring outside the lines wouldn't hurt.
The example card is for my service technician (Colin Marsh). If possible I would like to be able to edit the text to use for more than one person.

Industry/Entity Type

Appliance Repair

Contact Information for Business Card

Clean, crisp and professional but needs to be eye catching. Preferably using the black, white and red colour scheme matching the website. Double sided would be nice, but is not necessary.

Colors
ec1f27
ffffff
000000

Requirements
Must have
• Must be able to edit name, phone number and title to use for multiple people. Must show the company website (brightloopservice.ca).

```html
<!DOCTYPE html>
<html lang="en">
<head>
<meta charset="utf-8">
<title>Brightloop Service – Business Card</title>
<link href="https://fonts.googleapis.com/css2?family=Arvo:ital,wght@0,400;0,700;1,400&display=swap" rel="stylesheet">
<style>
  :root {
    --page: #e9e7e4;
    --card-front: #050505;
    --card-back: #262628;
    --red: #ec1f27;
    --white: #ffffff;
    --rule: #8a8a8c;
    --art-light: #4a4a4e;
    --art-dark: #141416;
  }
  * { box-sizing: border-box; margin: 0; padding: 0; }
  html, body {
    width: 1200px; height: 780px; overflow: hidden;
    background: var(--page);
    font-family: "Arvo", Georgia, serif;
  }
  .sheet {
    width: 1200px; height: 780px;
    display: flex; align-items: center; justify-content: center; gap: 40px;
  }
  .card {
    position: relative;
    width: 520px; height: 297px;
    border-radius: 4px;
    overflow: hidden;
    box-shadow: 0 10px 28px rgba(0,0,0,.25);
    color: var(--white);
  }
  .card--front { background: var(--card-front); }
  .card--back { background: var(--card-back); }

  .mascot-art {
    position: absolute;
    border-radius: 50% 50% 12px 12px;
    background: radial-gradient(ellipse at 50% 40%, var(--art-light), var(--art-dark) 75%);
  }
  .card--front .mascot-art { left: 218px; top: 42px; width: 150px; height: 140px; }
  .card--back .mascot-art { left: 70px; top: 40px; width: 150px; height: 150px; }

  .brand-name {
    position: absolute;
    font-weight: 700;
    color: var(--red);
    letter-spacing: 1px;
  }
  .card--front .brand-name { left: 170px; top: 180px; font-size: 30px; }
  .card--back .brand-name { left: 40px; top: 190px; font-size: 30px; }

  .tagline {
    position: absolute; left: 40px; right: 40px; top: 238px;
    font-style: italic; font-size: 13.5px; text-align: center;
  }

  .divider {
    position: absolute; left: 272px; top: 38px; width: 1px; height: 196px;
    background: var(--rule);
  }
  .contact { position: absolute; left: 296px; top: 40px; font-size: 13px; line-height: 1.45; }
  .contact__name { font-size: 18px; font-weight: 700; line-height: 1.1; }
  .contact__title { color: var(--red); font-size: 12.5px; margin-bottom: 10px; }
  .contact__address { margin-bottom: 8px; }
  .contact__line { display: flex; align-items: center; gap: 8px; }
  .contact__line svg { width: 12px; height: 12px; flex: none; fill: var(--red); }
  .contact__web { margin-top: 12px; font-size: 13.5px; }
  .contact__web .domain { color: var(--red); }

  .stripe {
    position: absolute; left: 0; right: 0; bottom: 0; height: 9px;
    display: flex;
  }
  .stripe__white { flex: 0 0 62%; background: var(--white); }
  .stripe__red { flex: 1; background: var(--red); }
</style>
</head>
<body>
<main class="sheet">
  <section class="card card--front" aria-label="Business card front">
    <div class="mascot-art" role="img" aria-label="Line illustration of a muscular technician in a hard hat holding a wrench"></div>
    <div class="brand-name">BRIGHTLOOP</div>
    <p class="tagline">when your equipment can't finish the workout, give us a call !</p>
  </section>

  <section class="card card--back" aria-label="Business card back">
    <div class="mascot-art" role="img" aria-label="Line illustration of a muscular technician in a hard hat holding a wrench"></div>
    <div class="brand-name">BRIGHTLOOP</div>
    <div class="divider"></div>
    <div class="contact">
      <div class="contact__name">Colin Marsh</div>
      <div class="contact__title">service technician</div>
      <div class="contact__address">118 Fenwick Road NW<br>Calgary AB T2K 4B7</div>
      <div class="contact__line">
        <svg viewBox="0 0 12 12" aria-hidden="true"><rect x="3" y="0" width="6" height="12" rx="1.2"/><rect x="4" y="1.5" width="4" height="7" fill="#262628"/></svg>
        <span>555-310-4821</span>
      </div>
      <div class="contact__line">
        <svg viewBox="0 0 12 12" aria-hidden="true"><path d="M1 4 Q6 0 11 4 L9.5 5.5 L8 4.5 L4 4.5 L2.5 5.5Z"/><rect x="2" y="6" width="8" height="5" rx="1"/></svg>
        <span>555-602-1938</span>
      </div>
      <div class="contact__line">
        <svg viewBox="0 0 12 12" aria-hidden="true"><rect x="0" y="2" width="12" height="8"/><path d="M0 2 L6 7 L12 2" stroke="#262628" stroke-width="1" fill="none"/></svg>
        <span>hello@brightloopservice.ca</span>
      </div>
      <div class="contact__web">www.<span class="domain">brightloopservice</span>.ca</div>
    </div>
    <div class="stripe"><span class="stripe__white"></span><span class="stripe__red"></span></div>
  </section>
</main>
</body>
</html>
```